Garlic Farm for Farm Sales/Restaurant sales

Need a professional, but appealing to agriculture world. We are selling 27 kinds of Organic Garlic from a farm in Simla,CO. I have uploaded logo and business information-we are going to need a template, because I will need to use it for four separate people.
-We are trying to appeal to Farm to table restaurants
-As well as growers/farmers

Target Market(s)

Agriculture Sales/Restaurants-Organic

Industry/Entity Type

Agriculture

Contact Information for Business Card

Want it to look more unique then your average kelto stock card- I want it to look amazing

Font styles to use
Sans Serif

Colors
0455a3
ec1f27
fbed22
ffffff

Requirements
Must have
• Just be creative
Nice to have
• Colorful
Should not have
• plain

```html
<!DOCTYPE html>
<html lang="en">
<head>
<meta charset="utf-8">
<title>Ridgeline Garlic – Business Card</title>
<link href="https://fonts.googleapis.com/css2?family=Open+Sans:wght@400;600&display=swap" rel="stylesheet">
<style>
  :root {
    --navy: #1b3466;
    --red: #c8102e;
    --yellow: #fdd000;
    --white: #ffffff;
    --ink: #555a60;
    --rule: #c9c9c9;
    --stage: #e8e5e1;
    --pattern-navy: #1e3a6e;
    --pattern-teal: #27506a;
  }
  * { box-sizing: border-box; margin: 0; padding: 0; }
  html, body { width: 1200px; height: 987px; overflow: hidden; }
  body {
    background: var(--stage);
    font-family: "Open Sans", Arial, sans-serif;
    position: relative;
  }
  .card {
    position: absolute;
    left: 292px;
    width: 616px;
    height: 352px;
    overflow: hidden;
  }
  .card--front { top: 130px; background: var(--white); }
  .card--back { top: 505px; background: var(--navy); }

  /* front */
  .brand {
    position: absolute;
    left: 66px;
    top: 104px;
    width: 212px;
    text-align: center;
  }
  .brand__dot {
    display: block;
    width: 88px;
    height: 88px;
    margin: 0 auto 12px;
    border-radius: 50%;
    background: var(--red);
  }
  .brand__name {
    color: var(--navy);
    font-weight: 600;
    font-size: 26px;
    line-height: 1.1;
  }
  .divider {
    position: absolute;
    left: 313px;
    top: 90px;
    width: 1px;
    height: 190px;
    background: var(--rule);
  }
  .contact {
    position: absolute;
    left: 355px;
    top: 92px;
  }
  .contact__name {
    color: var(--navy);
    font-weight: 600;
    font-size: 21px;
    line-height: 1.2;
  }
  .contact__role {
    color: var(--red);
    font-size: 16px;
    line-height: 1.3;
    margin-bottom: 12px;
  }
  .contact__address {
    color: var(--ink);
    font-size: 16px;
    line-height: 1.4;
    margin-bottom: 8px;
  }
  .contact__line {
    display: flex;
    align-items: center;
    gap: 8px;
    color: var(--ink);
    font-size: 16px;
    line-height: 23px;
  }
  .contact__line svg { width: 14px; height: 14px; fill: var(--navy); flex: none; }
  .stripe {
    position: absolute;
    left: 0; bottom: 0;
    width: 100%;
    height: 14px;
    display: flex;
  }
  .stripe span { flex: 1; }
  .stripe__red { background: var(--red); }
  .stripe__yellow { background: var(--yellow); }
  .stripe__navy { background: var(--navy); }

  /* back */
  .back__pattern {
    position: absolute;
    inset: 0;
    background: radial-gradient(circle at 50% 50%, var(--pattern-navy), var(--navy) 75%);
  }
  .back__brand {
    position: absolute;
    left: 0; width: 100%;
    top: 140px;
    text-align: center;
    color: var(--white);
    font-weight: 600;
    font-size: 40px;
    line-height: 1;
  }
  .social {
    position: absolute;
    left: 0; width: 100%;
    top: 279px;
    display: flex;
    justify-content: center;
    gap: 5px;
  }
  .social span {
    width: 22px; height: 22px;
    border: 1.5px solid var(--white);
    border-radius: 50%;
  }
</style>
</head>
<body>
  <section class="card card--front">
    <div class="brand">
      <span class="brand__dot"></span>
      <div class="brand__name">Ridgeline Garlic</div>
    </div>
    <div class="divider"></div>
    <div class="contact">
      <div class="contact__name">DALE HARMON</div>
      <div class="contact__role">CEO/FOUNDER</div>
      <div class="contact__address">P.O. Box 48 Prairie Fork<br>CO&nbsp; 80911</div>
      <div class="contact__line">
        <svg viewBox="0 0 16 16"><path d="M3.6 1.2l2.3 2.6-1.4 1.9c.9 2 2.5 3.7 4.6 4.8l1.9-1.4 2.7 2.2-1.3 2.8C6.9 14.2 1.7 9 1 3z"/></svg>
        719-555-0186
      </div>
      <div class="contact__line">
        <svg viewBox="0 0 16 16"><path d="M1 3h14v10H1z M2.5 4.5v.4L8 9l5.5-4.1v-.4z" fill-rule="evenodd"/></svg>
        Dale@RidgelineGarlic.com
      </div>
      <div class="contact__line">
        <svg viewBox="0 0 16 16"><path d="M8 1a7 7 0 1 0 0 14A7 7 0 0 0 8 1zm-1 2.2c-.3 1.2-1.8 1.5-2.3 2.6.8.7 2 .2 2.6 1.2-.4 1.2.8 2 .5 3.3-.3 1 .2 2.2.9 2.4A5.2 5.2 0 0 1 7 3.2zm3 .4c.9.4 1.6 1 2.1 1.8-.9.3-1.8-.2-2.2-1z"/></svg>
        www.RidgelineGarlic.com
      </div>
    </div>
    <div class="stripe">
      <span class="stripe__red"></span>
      <span class="stripe__yellow"></span>
      <span class="stripe__navy"></span>
    </div>
  </section>

  <section class="card card--back">
    <div class="back__pattern" role="img" aria-label="Repeating pattern of garlic bulbs in muted teal on navy"></div>
    <div class="back__brand">Ridgeline Garlic</div>
    <div class="social">
      <span></span><span></span><span></span><span></span>
    </div>
  </section>
</body>
</html>
```